Consulting firm business card, email signature, stationery
Brightmoor Advisory Collective
Use standard fonts
Same font or standard is fine
Daniel R. Hoskett
President
742 S. Tolliver Street
Clayton, MO 63190
dan.hoskett@brightmoorac.com
brightmoorac.com
The font can be standard for a professional consulting firm, or you can try with matching the logo.
The business card and email signature are most important. Stationery would be a nice bonus.
Ai version of logo file

```html
<!DOCTYPE html>
<html lang="en">
<head>
<meta charset="utf-8">
<title>Brightmoor Advisory Collective – Business Card</title>
<link href="https://fonts.googleapis.com/css2?family=Open+Sans:wght@400;600;700&display=swap" rel="stylesheet">
<style>
  :root {
    --page-bg: #e9e6e1;
    --card-bg: #ffffff;
    --brand-blue: #1f5fa8;
    --brand-green: #3f8a2e;
    --brand-orange: #f07a1e;
    --text-gray: #555a60;
    --rule-blue: #2c4f86;
    --faint: rgba(31, 95, 168, 0.07);
  }
  * { box-sizing: border-box; margin: 0; padding: 0; }
  html, body {
    width: 1200px; height: 466px; overflow: hidden;
    background: var(--page-bg);
    font-family: "Open Sans", Arial, sans-serif;
  }
  .card {
    position: absolute;
    top: 88px;
    width: 504px; height: 293px;
    background: var(--card-bg);
    box-shadow: 0 3px 10px rgba(0,0,0,0.25);
    overflow: hidden;
  }
  .card--front { left: 77px; }
  .card--back { left: 629px; }

  .brand {
    position: absolute; left: 26px; top: 34px;
    display: flex; align-items: center; gap: 10px;
  }
  .brand__dot {
    width: 40px; height: 40px; border-radius: 50%;
    background: var(--brand-blue);
  }
  .brand__name {
    font-weight: 700; font-size: 15px; line-height: 1.2;
    color: var(--brand-blue); text-transform: uppercase; letter-spacing: 0.5px;
  }

  .watermark {
    position: absolute; right: 48px; top: 96px;
    width: 170px; height: 170px; border-radius: 50%;
    background: var(--faint);
  }

  .person {
    position: absolute; left: 26px; top: 126px;
    font-size: 13px; font-weight: 700; color: var(--brand-green);
    text-transform: uppercase;
  }
  .person__title { font-weight: 400; color: var(--text-gray); text-transform: none; }
  .person-rule {
    position: absolute; left: 26px; top: 148px;
    width: 200px; height: 2px; background: var(--rule-blue);
  }

  .contacts {
    position: absolute; left: 26px; top: 160px;
    list-style: none; font-size: 11px; color: var(--text-gray);
  }
  .contacts li { display: flex; align-items: center; gap: 8px; height: 18px; }
  .contacts svg { width: 10px; height: 10px; fill: var(--text-gray); }

  .address {
    position: absolute; left: 26px; top: 245px;
    font-size: 11px; color: var(--text-gray);
  }

  .back-mark {
    position: absolute; left: 0; right: 0; top: 86px;
    display: flex; flex-direction: column; align-items: center; gap: 12px;
  }
  .back-mark .brand__dot { width: 74px; height: 74px; }
  .back-mark .brand__name { font-size: 15px; text-align: center; }
  .back-url {
    position: absolute; left: 0; right: 0; top: 240px;
    text-align: center; font-size: 11px; letter-spacing: 3px; color: var(--text-gray);
  }
</style>
</head>
<body>
  <section class="card card--front">
    <div class="watermark" aria-hidden="true"></div>
    <div class="brand">
      <span class="brand__dot" aria-hidden="true"></span>
      <span class="brand__name">Brightmoor<br>Advisory Collective</span>
    </div>
    <p class="person">Daniel R. Hoskett <span class="person__title">/ President</span></p>
    <div class="person-rule"></div>
    <ul class="contacts">
      <li><svg viewBox="0 0 10 10"><path d="M2 0h2l1 3-1.5 1a6 6 0 0 0 2.5 2.5L7 5l3 1v2c0 1-1 2-2 2A8 8 0 0 1 0 2c0-1 1-2 2-2z"/></svg>314-555-0148</li>
      <li><svg viewBox="0 0 10 10"><rect x="2" y="0" width="6" height="10" rx="1"/></svg>314-555-0193</li>
      <li><svg viewBox="0 0 10 10"><path d="M0 2h10v6H0z M0 2l5 3.5L10 2" /></svg>dan.hoskett@brightmoorac.com</li>
      <li><svg viewBox="0 0 10 10"><circle cx="5" cy="5" r="5"/></svg>www.brightmoorac.com</li>
    </ul>
    <p class="address">742 S. Tolliver Street, Clayton, MO 63190</p>
  </section>

  <section class="card card--back">
    <div class="back-mark">
      <span class="brand__dot" aria-hidden="true"></span>
      <span class="brand__name">Brightmoor Advisory Collective</span>
    </div>
    <p class="back-url">www.brightmoorac.com</p>
  </section>
</body>
</html>
```